Coffee and Plastics

I am looking for a completely new site that shows the products we have. Our current site is www.velmorebrothersbeans.com. We are open minded to what designers come up with. Our current site is www.velmorebrothersbeans.com. You can you the information from there to start the site. I need these tabs on the main home page. ( Home, Coffee & Tea, Condiments, and Paper and Plastics, and Contact.) You can take photos and info from my Current site. In products page.
I will be uploading info and photo for paper and plastics.
Look and feel
Each slider illustrates characteristics of the customer's brand and the style your logo design should communicate.

```html
<!DOCTYPE html>
<html lang="en">
<head>
<meta charset="utf-8">
<title>Velmore Brothers Beans</title>
<link href="https://fonts.googleapis.com/css2?family=Montserrat:wght@400;500;600&family=Source+Sans+3:wght@400;600&display=swap" rel="stylesheet">
<style>
  :root {
    --accent: #b8690f;
    --accent-dark: #a85c08;
    --ink: #3b3b3b;
    --body: #707070;
    --nav: #6a6a6a;
    --band: #f4f2f1;
    --footer: #3d3d3d;
    --footer-text: #e4e4e4;
    --white: #ffffff;
  }
  * { box-sizing: border-box; margin: 0; padding: 0; }
  html, body { width: 862px; height: 1200px; overflow: hidden; background: var(--white); }
  body { position: relative; font-family: "Source Sans 3", Arial, sans-serif; color: var(--body); }
  .abs { position: absolute; }

  /* header */
  .brand-mark { left: 94px; top: 18px; width: 43px; height: 41px; border-radius: 4px; background: linear-gradient(#c77a1c, var(--accent-dark)); }
  .brand-name { left: 150px; top: 16px; font-family: "Montserrat", sans-serif; font-size: 18px; line-height: 23px; color: var(--ink); }
  .phone { right: 95px; top: 14px; display: flex; align-items: center; gap: 6px; font-size: 10px; color: var(--nav); }
  .phone strong { font-family: "Montserrat", sans-serif; font-weight: 400; font-size: 15px; color: var(--accent); }
  .main-nav { right: 95px; top: 49px; display: flex; font-size: 10px; color: var(--nav); }
  .main-nav span + span::before { content: "|"; margin: 0 12px; color: #888; }
  .main-nav .current { color: var(--accent); }

  /* hero */
  .hero { left: 0; top: 80px; width: 862px; height: 338px; background: radial-gradient(circle at 660px 170px, #b5906a 0, #9a7452 95px, #4a2614 112px, #3a1c0e 60%, #2b140a 100%); }
  .hero-title { left: 96px; top: 172px; font-family: "Montserrat", sans-serif; font-weight: 600; font-size: 26px; color: var(--white); }
  .hero-text { left: 96px; top: 224px; width: 380px; font-size: 11px; line-height: 19px; color: var(--white); }
  .btn { display: flex; align-items: center; justify-content: center; color: var(--white); background: linear-gradient(#c27519, var(--accent-dark)); border-radius: 2px; font-size: 9.5px; }
  .hero-btn { left: 96px; top: 282px; width: 100px; height: 31px; font-size: 11px; }
  .dots { left: 101px; top: 389px; display: flex; gap: 5px; }
  .dots i { width: 10px; height: 10px; border-radius: 50%; background: var(--accent); }
  .dots i:first-child { background: var(--white); }

  /* sections */
  .section-title { font-family: "Montserrat", sans-serif; font-size: 18px; color: var(--ink); }
  .section-title em { font-style: normal; color: var(--accent); }
  .welcome-title { left: 0; width: 862px; top: 460px; text-align: center; }
  .welcome-text { left: 94px; width: 674px; text-align: center; font-size: 9.6px; line-height: 17.5px; }
  .welcome-btn { left: 390px; top: 610px; width: 80px; height: 27px; }

  .featured { left: 0; top: 670px; width: 862px; height: 220px; background: var(--band); }
  .featured-photo { left: 94px; top: 706px; width: 209px; height: 149px; background: radial-gradient(circle at 60% 55%, #6b3d1c, #2a1608 75%); }
  .featured-title { left: 325px; top: 702px; }
  .featured-text { left: 325px; top: 741px; width: 441px; font-size: 9.6px; line-height: 17.2px; }
  .featured-btn { left: 326px; top: 828px; width: 80px; height: 27px; }

  .serving-title { left: 0; width: 862px; top: 937px; text-align: center; }
  .next-arrow { left: 746px; top: 942px; }
  .products { left: 94px; top: 986px; width: 675px; height: 100px; }
  .product { position: absolute; top: 0; width: 100px; text-align: center; font-size: 10px; color: var(--ink); }
  .product-photo { height: 71px; margin-bottom: 9px; }

  /* footer */
  .site-footer { left: 0; top: 1122px; width: 862px; height: 78px; background: var(--footer); }
  .footer-nav { left: 81px; top: 1145px; display: flex; font-size: 9.6px; color: var(--footer-text); }
  .footer-nav span + span::before { content: "/"; margin: 0 8px; }
  .copyright { left: 81px; top: 1168px; font-size: 9.6px; color: var(--footer-text); }
  .social { left: 656px; top: 1149px; display: flex; gap: 5px; }
  .social i { width: 24px; height: 24px; border-radius: 50%; background: #e8e8e8; }
</style>
</head>
<body>
  <!-- header -->
  <div class="abs brand-mark"></div>
  <div class="abs brand-name">Velmore<br>Brothers Beans</div>
  <div class="abs phone">
    <svg width="11" height="8" viewBox="0 0 11 8"><path d="M0 3 Q5.5 -1 11 3 L10 4.5 L8 3.5 L8 2.5 Q5.5 1.5 3 2.5 L3 3.5 L1 4.5Z M2.5 4.5 L8.5 4.5 L9.5 8 L1.5 8Z" fill="#b8690f"/></svg>
    Call <strong>1-800-555-0142</strong>
  </div>
  <nav class="abs main-nav">
    <span class="current">Home</span><span>Coffee &amp; Tea</span><span>Condiments</span><span>Paper</span><span>Plastics</span><span>Contact</span>
  </nav>

  <!-- hero -->
  <div class="abs hero" role="img" aria-label="Roasted coffee beans surrounding a burlap circle"></div>
  <h1 class="abs hero-title">Aromatic &amp; Robust Coffees</h1>
  <p class="abs hero-text">Velmore Brothers is continuously striving for ways to improve quality and product appearance to meet the highest standards in today's franchises</p>
  <a class="abs btn hero-btn">Learn More ››</a>
  <div class="abs dots"><i></i><i></i><i></i><i></i></div>

  <!-- welcome -->
  <h2 class="abs section-title welcome-title">Welcome to <em>Velmore Brothers Beans</em></h2>
  <p class="abs welcome-text" style="top:501px">We are a family-owned and operated business based in Cedar Ridge Texas. Since the opening of Velmore Brothers Beans plant in 1995, we have become Texas' premier independently owned coffee packaging company. Our success relies solely on the principle of selling only the freshest, highest-quality in-room coffee available.</p>
  <p class="abs welcome-text" style="top:554px">Velmore Brothers packages and supplies in-room coffee, tea products, and condiments. Whether we're supplying a 50-room Hotel or a 500-room grand resort, we have the distribution capacity to fill your rooms with the most aromatic and robust coffees and teas available at competitive prices.</p>
  <a class="abs btn welcome-btn">Learn More ››</a>

  <!-- featured -->
  <div class="abs featured"></div>
  <div class="abs featured-photo" role="img" aria-label="Metal scoops in a burlap sack of coffee beans"></div>
  <h2 class="abs section-title featured-title">Featured <em>Products</em></h2>
  <p class="abs featured-text">Velmore Brothers is continuously striving for ways to improve quality and product appearance to meet the highest standards in today's franchises and independent hotels. We are very aware that our success depends entirely upon maintaining our customers' confidence in our products, so we pay close attention to your needs every step of the way.</p>
  <a class="abs btn featured-btn">Learn More ››</a>

  <!-- serving -->
  <h2 class="abs section-title serving-title">Serving Fine Establishments <em>Everywhere!</em></h2>
  <svg class="abs next-arrow" width="22" height="22" viewBox="0 0 22 22"><circle cx="11" cy="11" r="10" fill="#fff" stroke="#cfcfcf"/><path d="M8 6 L15 11 L8 16 L10 11Z" fill="#c4c4c4"/></svg>
  <div class="abs products">
    <div class="product" style="left:0"><div class="product-photo" role="img" aria-label="Gold round compartment tray" style="background:linear-gradient(#c9a65a,#8a6a2a)"></div>Neque porro</div>
    <div class="product" style="left:114px;width:98px"><div class="product-photo" role="img" aria-label="White round compartment plate" style="background:radial-gradient(#f2f2f2 45%,#2a2a2a 72%)"></div>Quisquam</div>
    <div class="product" style="left:229px"><div class="product-photo" role="img" aria-label="Paper coffee cup with lid" style="background:linear-gradient(90deg,#f3f3f3 40%,#b48a63 60%)"></div>Est qui dolorem</div>
    <div class="product" style="left:344px"><div class="product-photo" role="img" aria-label="Silver rectangular compartment tray" style="background:linear-gradient(#9a9ea4,#3a3c40)"></div>Ipsum quia</div>
    <div class="product" style="left:459px"><div class="product-photo" role="img" aria-label="Gold rectangular compartment tray" style="background:linear-gradient(#d8b56a,#a07a30)"></div>Dolor sit amet</div>
    <div class="product" style="left:579px;width:96px"><div class="product-photo" role="img" aria-label="Clear round compartment tray" style="background:radial-gradient(#cfd2d6 45%,#1e1e1e 75%)"></div>Consectetur</div>
  </div>

  <!-- footer -->
  <footer class="abs site-footer"></footer>
  <nav class="abs footer-nav"><span>Home</span><span>Coffee &amp; Tea</span><span>Condiments</span><span>Paper</span><span>Plastics</span><span>Contact</span></nav>
  <p class="abs copyright">©2014. Your site. All rights reserved.</p>
  <div class="abs social" aria-label="Social links"><i></i><i></i><i></i><i></i></div>
</body>
</html>
```